Home Remodeler Needs a Website!

Single page (plus contact form) website for small home remodeling company. He's got a few pictures he'd like on the site and needs some basic text. He likes clean, simple designs and is "more traditional" in his stylistic preferences. Most of his business comes from word-of-mouth advertising and so the site is just something he needs for people to feel more comfortable with his business.

Target Market(s)

People who want to remodel their homes

Coding

Coded - Design and coding required

Number of Pages Required

2 page

Requirements
Must have
• Main page to include some or all of the attached images, contact page. Neutral colors. Old domain: lindcroftmeadowbuild.com New domain: qm-ventureworks.com You can pull text from the old site or update it.
Should not have
• No loud colors/loud visual elements

```html
<!DOCTYPE html>
<html lang="en">
<head>
<meta charset="utf-8">
<title>Lindcroft Meadow Build</title>
<link href="https://fonts.googleapis.com/css2?family=Roboto:ital,wght@0,400;0,500;0,700;0,900;1,400&display=swap" rel="stylesheet">
<style>
:root{
  --accent:#a07d5e;
  --accent-deep:#8a6b50;
  --band:#8f7d6b;
  --dark:#34383d;
  --ink:#1f2226;
  --grey:#6b6b6b;
  --light:#f3f2ef;
  --white:#fff;
  --social:#8b8f94;
}
*{box-sizing:border-box;margin:0;padding:0}
html,body{width:1200px;height:4651px;overflow:hidden}
body{font-family:'Roboto',sans-serif;color:var(--ink);background:var(--white);position:relative}
.abs{position:absolute}
.accent{color:var(--accent)}
.f-accent{fill:var(--accent)}
.f-dark{fill:var(--dark)}
.f-white{fill:#fff}
.s-accent{stroke:var(--accent)}
.s-dark{stroke:var(--dark)}

/* header */
.header{top:0;left:0;width:1200px;height:110px}
.brand{left:112px;top:22px;display:flex;align-items:center;gap:14px}
.brand-mark{width:44px;height:60px;background:var(--dark)}
.brand-name{font-weight:700;font-size:18px;line-height:22px;color:var(--dark);text-transform:uppercase}
.follow{left:648px;top:32px;display:flex;align-items:center;gap:8px;font-size:11px;font-weight:500}
.social{width:24px;height:24px;border-radius:50%;display:inline-block;background:var(--social)}
.callus{left:910px;top:20px;display:flex;gap:14px;align-items:center}
.callus small{display:block;font-size:10px;font-weight:500}
.callus b{font-size:19px;color:var(--accent)}
.nav{left:473px;top:80px;display:flex;gap:22px;font-size:13px;font-weight:700;text-transform:uppercase}
.nav a{color:var(--ink);text-decoration:none;padding-bottom:10px}
.nav a.active{color:var(--accent);border-bottom:3px solid var(--accent)}

/* hero */
.hero{top:110px;left:0;width:1200px;height:702px;
  background:linear-gradient(90deg,#4a4b44 0%,#76726a 20%,#a8a6a1 45%,#8d8a84 60%,#4f5866 80%,#3f4857 100%)}
.hero::after{content:"";position:absolute;inset:0;background:rgba(0,0,0,.32)}
.hero-text{top:190px;left:0;width:1200px;text-align:center;color:#fff;z-index:2}
.hero-text h1{font-size:34px;font-weight:700;text-transform:uppercase}
.hero-text p{font-size:16px;font-weight:500;width:560px;margin:10px auto 0;line-height:27px}
.btn{display:inline-block;background:var(--accent);color:#fff;font-weight:700;font-size:15px;text-transform:uppercase;border-radius:30px;text-decoration:none}
.hero .btn{position:absolute;left:506px;top:330px;width:186px;height:48px;line-height:48px;text-align:center;z-index:2}
.hero-edge{left:0;top:560px;z-index:3}

/* welcome */
.welcome-title{top:830px;left:0;width:1200px;text-align:center;font-size:30px;font-weight:700;text-transform:uppercase}
.welcome-copy{top:892px;left:170px;width:860px;text-align:center;font-size:13.5px;line-height:25px;color:var(--grey)}
.feature{top:988px;display:flex;align-items:center;gap:18px;font-size:15px;font-weight:500;line-height:23px}
.hex{width:78px;height:86px;background:var(--accent);clip-path:polygon(50% 0,100% 25%,100% 75%,50% 100%,0 75%,0 25%);display:flex;align-items:center;justify-content:center}
.hex span{width:34px;height:34px;border:3px solid #fff;border-radius:50%}

/* about */
.about-bg{top:1152px;left:0;width:1200px;height:545px;background:var(--light)}
.about-label{top:1246px;left:112px;display:flex;align-items:center;gap:14px;color:var(--accent);font-weight:700;font-size:18px}
.about-label i{width:56px;height:2px;background:var(--accent)}
.about-title{top:1274px;left:110px;font-size:31px;font-weight:700}
.about-copy{top:1328px;left:112px;width:490px;font-size:13.5px;line-height:25px;color:#555}
.about-copy p{margin-bottom:8px}
.btn-outline{top:1567px;left:110px;width:166px;height:44px;line-height:40px;border:2px solid var(--accent);border-radius:24px;color:var(--accent);font-weight:700;font-size:14px;text-align:center;text-transform:uppercase}
.about-photo{top:1212px;left:696px;width:394px;height:450px}

/* services */
.services-bg{top:1690px;left:0;width:1200px;height:740px}
.services-title{top:1810px;left:0;width:1200px;text-align:center;color:#fff;font-size:40px;font-weight:700;text-transform:uppercase}
.divider{top:1868px;left:508px;width:184px;height:12px}
.diagram{top:1900px;left:0;width:1200px;height:460px}
.svc-label{fill:#fff;font-family:'Roboto',sans-serif;font-weight:700;font-size:16px}

/* package */
.kicker{top:2502px;left:0;width:1200px;text-align:center;color:var(--accent);font-size:16px;font-weight:500}
.package-title{top:2530px;left:0;width:1200px;text-align:center;font-size:38px;font-weight:700;text-transform:uppercase}
.card{top:2622px;width:310px;height:356px;background:#fff;box-shadow:0 2px 14px rgba(0,0,0,.12);border-radius:6px;text-align:center;padding:6px}
.card .pic{height:202px;border-radius:4px}
.card h3{font-size:16px;font-weight:700;margin-top:24px}
.card p{font-size:13.5px;line-height:22px;color:var(--grey);margin:12px 16px 0}
.card a{display:block;margin-top:14px;color:var(--accent);font-weight:700;font-size:14px;text-decoration:none}
.arrow{top:2780px;width:30px;height:44px}

/* testimonial */
.testimonial{top:3073px;left:0;width:1200px;height:325px;background:var(--band)}
.testimonial h2{top:55px;left:320px;color:#fff;font-size:34px;font-weight:700;text-transform:uppercase}
.avatar{top:99px;left:164px;width:136px;height:136px;background:linear-gradient(135deg,#b9c3cc,#7d8b97);transform:rotate(45deg);border:5px solid #fff;border-radius:10px}
.quote{top:129px;left:322px;width:680px;color:#fff;font-style:italic;font-size:15px;line-height:27px}
.quote-mark{color:rgba(255,255,255,.5);font-size:64px;font-weight:900}
.author{top:222px;left:322px;color:#fff}
.author b{font-size:17px;font-weight:700;display:block}
.author small{font-size:11px}

/* projects */
.projects-title{top:3482px;left:0;width:1200px;text-align:center;font-size:36px;font-weight:700;text-transform:uppercase}
.shot{position:absolute}

/* footer */
.footer-bg{top:4150px;left:0;width:1200px;height:501px}
.footer-brand{top:4330px;left:140px;width:170px;text-align:center;color:#fff}
.footer-brand .brand-mark{width:80px;height:100px;background:#fff;margin:0 auto 20px}
.footer-brand b{font-size:17px;line-height:22px;font-weight:700;text-transform:uppercase}
.footer-social{top:4502px;left:162px;display:flex;gap:14px}
.footer-social span{width:12px;height:12px;border-radius:50%;background:#fff}
.fcol{color:#fff;font-size:13px}
.fcol h4{font-size:16px;font-weight:700;margin-bottom:24px}
.fcol ul{list-style:none;line-height:26px}
.contact-item{display:flex;gap:10px;margin-bottom:14px;line-height:17px}
.contact-item b{display:block;font-size:11px}
.contact-item .ico{color:var(--accent);width:12px}
.fcol .btn{width:200px;height:40px;line-height:40px;text-align:center;font-size:14px;margin-top:20px}
.gotop{top:4578px;left:1022px;color:#fff;font-size:11px;font-weight:700}
.bottom{top:4594px;left:112px;width:976px;border-top:1px solid rgba(255,255,255,.25);padding-top:16px;display:flex;justify-content:space-between;color:#fff;font-size:13px}
</style>
</head>
<body>

<header class="header abs">
  <div class="brand abs"><span class="brand-mark"></span><span class="brand-name">Lindcroft Meadow<br>Build</span></div>
  <div class="follow abs">FOLLOW US:
    <span class="social" aria-label="social profile"></span>
    <span class="social" aria-label="social profile"></span>
    <span class="social" aria-label="social profile"></span>
    <span class="social" aria-label="social profile"></span>
  </div>
  <div class="callus abs">
    <svg width="26" height="26" viewBox="0 0 24 24" fill="none" stroke="#888" stroke-width="1.6"><path d="M5 3h4l2 5-3 2a12 12 0 0 0 6 6l2-3 5 2v4a2 2 0 0 1-2 2A18 18 0 0 1 3 5a2 2 0 0 1 2-2z"/></svg>
    <div><small>CALL US</small><b>555-014-6328</b></div>
  </div>
  <nav class="nav abs">
    <a class="active">Home</a><a>About Us</a><a>Our Services</a><a>Extras</a><a>Projects</a><a>Blog</a><a>Contact Us</a>
  </nav>
</header>

<section class="hero abs" role="img" aria-label="Remodeled kitchen with stainless appliances, farmhouse sink and painted walls">
  <div class="hero-text abs">
    <h1>Lindcroft Meadow Build</h1>
    <p>When you want affordable, quality home construction services; think of us to do the job.</p>
  </div>
  <a class="btn">Get Started</a>
  <svg class="hero-edge abs" width="1200" height="142" viewBox="0 0 1200 142">
    <polygon points="0,124 795,20 1200,108 1200,142 0,142" class="f-white"/>
    <polygon points="0,112 795,6 1200,96 1200,108 795,20 0,124" class="f-accent"/>
  </svg>
</section>

<section class="welcome">
  <h2 class="welcome-title abs">Welcome to Lindcroft <span class="accent">Meadow Build</span></h2>
  <p class="welcome-copy abs">Since 1981 Walter Bryce has built and remodeled over 400 homes and businesses. Let us be your contractor for the next project you start.When quality, value and personal attention to detail are important With over 20 years experience in residential and commercial construction, you can trust your project to Lindcroft Meadow Build.</p>
  <div class="feature abs" style="left:133px"><div class="hex"><span></span></div>We've Repution For<br>Excellence</div>
  <div class="feature abs" style="left:398px"><div class="hex"><span></span></div>We Build<br>Partnerships</div>
  <div class="feature abs" style="left:640px"><div class="hex"><span></span></div>Guided By<br>Commitment</div>
  <div class="feature abs" style="left:880px"><div class="hex"><span></span></div>A Team Of<br>Professionals</div>
</section>

<section class="about">
  <div class="about-bg abs"></div>
  <div class="about-label abs"><i></i>About Us</div>
  <h2 class="about-title abs">"DON'T TINKER AROUND"</h2>
  <div class="about-copy abs">
    <p>I have built my business with a partnership of clients, employees, subcontractors, suppliers and inspectors. Since each project is unique, this partnership brings creative ideas to your home.</p>
    <p>I have deep "hands on" history in construction from foundations to final finishing touches. We cultivate suppliers who deliver quality materials on time and without damage.</p>
    <p>Our subcontractors are our friends and will become yours too. When called upon to explain their part of the process, they are glad to.</p>
  </div>
  <div class="btn-outline abs">Learn More</div>
  <svg class="about-photo abs" viewBox="0 0 394 450" role="img" aria-label="Finished basement with polished concrete floor and kitchenette">
    <defs><linearGradient id="basement" x1="0" y1="0" x2="0" y2="1"><stop offset="0" stop-color="#b7b0a3"/><stop offset=".5" stop-color="#7d6a55"/><stop offset="1" stop-color="#4e3b2b"/></linearGradient></defs>
    <polygon points="197,2 392,114 392,336 197,448 2,336 2,114" fill="#fff"/>
    <polygon points="197,14 382,120 382,330 197,436 12,330 12,120" fill="url(#basement)"/>
  </svg>
</section>

<section class="services">
  <svg class="services-bg abs" viewBox="0 0 1200 740" preserveAspectRatio="none">
    <polygon points="0,98 350,8 1200,112 1200,630 830,740 0,620" class="f-dark"/>
    <polygon points="350,8 1200,108 1200,116 350,20" class="f-accent"/>
    <polygon points="350,0 0,92 0,100 350,10" class="f-accent"/>
    <polygon points="1200,622 830,732 820,740 1200,634" class="f-accent"/>
  </svg>
  <h2 class="services-title abs">Our Services</h2>
  <svg class="divider abs" viewBox="0 0 184 12"><line x1="0" y1="6" x2="70" y2="6" stroke="#fff"/><line x1="114" y1="6" x2="184" y2="6" stroke="#fff"/><circle cx="80" cy="6" r="4" class="f-accent"/><circle cx="92" cy="6" r="6" class="f-accent"/><circle cx="104" cy="6" r="4" class="f-accent"/></svg>
  <svg class="diagram abs" viewBox="0 0 1200 460">
    <path d="M318,470 C300,5 885,5 866,470" fill="none" stroke="#fff" stroke-width="8"/>
    <g fill="none" class="s-accent" stroke-width="2">
      <polyline points="107,322 265,322 300,360"/>
      <polyline points="122,178 275,178 330,228"/>
      <polyline points="219,76 375,76 420,130"/>
      <polyline points="812,78 975,78"/><polyline points="812,78 765,128"/>
      <polyline points="860,225 915,186 1075,186"/>
      <polyline points="895,348 940,316 1100,316"/>
    </g>
    <g transform="translate(320,374)"><circle r="40" class="f-accent"/><circle r="32" fill="#fff"/><rect x="-12" y="-14" width="24" height="28" fill="none" class="s-dark" stroke-width="3"/></g>
    <g transform="translate(363,253)"><circle r="40" class="f-accent"/><circle r="32" fill="#fff"/><circle r="12" fill="none" class="s-dark" stroke-width="3"/></g>
    <g transform="translate(451,160)"><circle r="40" class="f-accent"/><circle r="32" fill="#fff"/><rect x="-14" y="-12" width="28" height="24" class="f-dark"/></g>
    <g transform="translate(592,118)"><circle r="40" class="f-accent"/><circle r="32" fill="#fff"/><path d="M-12,-10h14v10h10v10" fill="none" class="s-dark" stroke-width="4"/></g>
    <g transform="translate(735,165)"><circle r="40" class="f-accent"/><circle r="32" fill="#fff"/><path d="M-14,2 0,-12 14,2v12h-28z" class="f-dark"/></g>
    <g transform="translate(825,257)"><circle r="40" class="f-accent"/><circle r="32" fill="#fff"/><rect x="-14" y="-8" width="28" height="20" class="f-dark"/></g>
    <g transform="translate(863,371)"><circle r="40" class="f-accent"/><circle r="32" fill="#fff"/><rect x="-12" y="-12" width="24" height="14" class="f-dark"/><rect x="-3" y="2" width="6" height="12" class="f-dark"/></g>
    <text x="107" y="312" class="svc-label">Window Replacement</text>
    <text x="122" y="168" class="svc-label">Electrical</text>
    <text x="219" y="66" class="svc-label">Roofing</text>
    <text x="476" y="40" class="svc-label">Air conditioning and plumbing</text>
    <text x="913" y="68" class="svc-label">Gutters</text>
    <text x="1008" y="176" class="svc-label">Painting</text>
    <text x="983" y="306" class="svc-label">Concrete work</text>
  </svg>
</section>

<section class="package">
  <div class="kicker abs">Commercial and Residential Contracting</div>
  <h2 class="package-title abs">All In One Package</h2>
  <svg class="arrow abs" style="left:36px" viewBox="0 0 30 44"><polyline points="24,4 6,22 24,40" fill="none" stroke="#999" stroke-width="4"/></svg>
  <svg class="arrow abs" style="left:1128px" viewBox="0 0 30 44"><polyline points="6,4 24,22 6,40" fill="none" stroke="#999" stroke-width="4"/></svg>
  <div class="card abs" style="left:110px"><div class="pic" role="img" aria-label="Construction workers on a building site" style="background:linear-gradient(180deg,#c9d3da,#8a6f5a)"></div><h3>New Construction</h3><p>Lorem ipsum dolor sit amet, consectetur adipiscing elit, sed do eiusmod</p><a>READ MORE ➔</a></div>
  <div class="card abs" style="left:445px"><div class="pic" role="img" aria-label="Wooden porch deck with steps" style="background:linear-gradient(180deg,#8fa37a,#a8784f)"></div><h3>Porches and Decks</h3><p>Lorem ipsum dolor sit amet, consectetur adipiscing elit, sed do eiusmod</p><a>READ MORE ➔</a></div>
  <div class="card abs" style="left:780px"><div class="pic" role="img" aria-label="Remodeled bathroom with tub and glass shower" style="background:linear-gradient(180deg,#aeb6b8,#7c7d78)"></div><h3>Remodeling / kitchens and baths</h3><p>Lorem ipsum dolor sit amet, consectetur adipiscing elit, sed do eiusmod</p><a>READ MORE ➔</a></div>
</section>

<section class="testimonial abs">
  <div class="avatar abs" role="img" aria-label="Client portrait"></div>
  <h2 class="abs">What Our Clients Have To Say</h2>
  <span class="quote-mark abs" style="top:96px;left:270px">“</span>
  <p class="quote abs">Lorem ipsum dolor sit amet, consectetur adipiscing elit, sed do eiusmod tempor incididunt ut labore et dolore magna aliqua. Ut enim ad minim veniam, quis nostrud exercitation ullamco laboris nisi ut aliquip ex ea commodo consequat.</p>
  <span class="quote-mark abs" style="top:176px;left:592px">”</span>
  <div class="author abs"><b>John Doe</b><small>Company Name</small></div>
</section>

<section class="projects">
  <h2 class="projects-title abs">Completed <span class="accent">Project</span></h2>
  <div class="shot" style="top:3560px;left:112px;width:488px;height:242px;background:linear-gradient(180deg,#b5ad9e,#5a4532)" role="img" aria-label="Finished basement living area"></div>
  <div class="shot" style="top:3560px;left:611px;width:231px;height:242px;background:linear-gradient(180deg,#3a2a22,#5e3f2a)" role="img" aria-label="Kitchen with dark wood cabinets"></div>
  <div class="shot" style="top:3560px;left:852px;width:231px;height:242px;background:linear-gradient(180deg,#c8b49a,#6f6258)" role="img" aria-label="Commercial building under construction"></div>
  <div class="shot" style="top:3814px;left:112px;width:231px;height:242px;background:linear-gradient(180deg,#a8b0b2,#7e7a74)" role="img" aria-label="Remodeled bathroom"></div>
  <div class="shot" style="top:3814px;left:353px;width:232px;height:242px;background:linear-gradient(180deg,#9fb3c8,#8d5e44)" role="img" aria-label="Backyard deck with railing"></div>
  <div class="shot" style="top:3814px;left:595px;width:488px;height:242px;background:linear-gradient(90deg,#6f6a5c,#a6a6a2 45%,#4f5866)" role="img" aria-label="Remodeled kitchen with steel appliances"></div>
</section>

<footer>
  <svg class="footer-bg abs" viewBox="0 0 1200 501" preserveAspectRatio="none">
    <polygon points="0,30 400,140 1200,30 1200,501 0,501" class="f-dark"/>
    <polygon points="0,12 400,128 1200,12 1200,22 400,140 0,24" class="f-accent"/>
  </svg>
  <div class="footer-brand abs"><div class="brand-mark"></div><b>Lindcroft Meadow<br>Build</b></div>
  <div class="footer-social abs"><span></span><span></span><span></span><span></span></div>
  <div class="fcol abs" style="top:4350px;left:369px">
    <h4>Our Office Address</h4>
    <div class="contact-item"><span class="ico">✆</span><div><b>Phone</b>555-016-7843</div></div>
    <div class="contact-item"><span class="ico">✉</span><div><b>Email</b>office@lindcroftmeadowbuild.com</div></div>
    <div class="contact-item"><svg class="ico" width="10" height="14" viewBox="0 0 10 14"><path d="M5 0a5 5 0 0 1 5 5c0 4-5 9-5 9S0 9 0 5a5 5 0 0 1 5-5z" class="f-accent"/></svg><div><b>Location</b>Crest House, 4 Linden Avenue,<br>Marlow Vale KV12 3QP</div></div>
  </div>
  <div class="fcol abs" style="top:4350px;left:671px">
    <h4>Company</h4>
    <ul><li>Home</li><li>Design &amp; Planning</li><li>Extensions</li><li>HMO's</li><li>Maintenance</li><li>References</li></ul>
  </div>
  <div class="fcol abs" style="top:4350px;left:862px;width:240px">
    <h4>Stil have questios?</h4>
    <p style="line-height:18px;font-size:12px">Contact us using this form. A repesentative will aswer your questions as soon as possible.</p>
    <a class="btn">Get A Quote</a>
  </div>
  <div class="gotop abs">▲ Go Up</div>
  <div class="bottom abs"><span>© 2021 Lindcroft Meadow Build. | All Rights Reserved</span><span>Privacy Policy &nbsp;|&nbsp; Cookie Policy &nbsp;|&nbsp; Terms Of Services</span></div>
</footer>

</body>
</html>
```